Northglint Name Card & Logo Design

We need a new business card design and a logo for our company as well. Our company is in the computer retail business. We provide our walk in customers with a wide range of computer products from mouse to complete desktop.Anything you need in a computer? We got it. Our area of aim is to provide customers with value and trust in our service & products .We provide customization of Computer desktop/ Repairs of laptop/desktop.
You may want to take a look at our Website for more information.
www.northglint-demo.com.sg
Industry/Entity Type
Computer
Contact Information for Business Card
Northglint Technology
Tan Wei Lun
Operations Manager
+65 6000 1472
+65 9000 3825
tanwl@northglint-demo.com.sg
Corporate Sales Enquries : corporatesales@northglint-demo.com.sg

```html
<!DOCTYPE html>
<html lang="en">
<head>
<meta charset="utf-8">
<title>Northglint Technology – Business Card</title>
<link rel="stylesheet" href="https://fonts.googleapis.com/css2?family=Montserrat:wght@400;500;600;700&display=swap">
<style>
  :root {
    --backdrop: #e4e6e9;
    --navy-deep: #0a1530;
    --navy-mid: #123a78;
    --navy-card: #0d1422;
    --cyan: #39a9e6;
    --white: #ffffff;
    --soft-white: #d9e1ea;
    --card-shadow: 0 18px 40px rgba(0, 0, 0, 0.35);
  }
  * { box-sizing: border-box; margin: 0; padding: 0; }
  html, body {
    width: 1200px;
    height: 800px;
    overflow: hidden;
    background: var(--backdrop);
    font-family: "Montserrat", sans-serif;
  }
  .canvas {
    position: relative;
    width: 1200px;
    height: 800px;
  }

  /* Front of card (portrait) */
  .card-front {
    position: absolute;
    left: 130px;
    top: 140px;
    width: 340px;
    height: 520px;
    background: radial-gradient(ellipse at 50% 35%, var(--navy-mid) 0%, #0e2656 50%, var(--navy-deep) 100%);
    box-shadow: var(--card-shadow);
    overflow: hidden;
    color: var(--white);
    text-align: center;
  }
  .circuit-texture {
    position: absolute;
    inset: 0;
    background:
      radial-gradient(ellipse at 30% 15%, rgba(57, 169, 230, 0.18), transparent 55%),
      radial-gradient(ellipse at 70% 90%, rgba(57, 169, 230, 0.14), transparent 50%);
  }
  .front-brand {
    position: absolute;
    left: 0;
    right: 0;
    top: 190px;
    display: flex;
    flex-direction: column;
    align-items: center;
    gap: 14px;
  }
  .brand-dot {
    width: 54px;
    height: 54px;
    border-radius: 50%;
    background: var(--cyan);
  }
  .brand-name {
    font-weight: 700;
    font-size: 27px;
    line-height: 1.05;
    letter-spacing: 0.5px;
    text-transform: uppercase;
    color: var(--white);
  }
  .front-web {
    margin-top: 4px;
    font-size: 16px;
    font-weight: 500;
    color: var(--white);
  }
  .tagline {
    position: absolute;
    left: 0;
    right: 0;
    bottom: 58px;
    line-height: 1.1;
  }
  .tagline-lead {
    display: block;
    font-size: 21px;
    font-weight: 500;
    color: var(--white);
  }
  .tagline-strong {
    display: block;
    font-size: 27px;
    font-weight: 700;
    color: var(--cyan);
  }

  /* Back of card (landscape) */
  .card-back {
    position: absolute;
    left: 530px;
    top: 230px;
    width: 560px;
    height: 340px;
    background: linear-gradient(160deg, #152033 0%, var(--navy-card) 60%, #080d17 100%);
    box-shadow: var(--card-shadow);
    overflow: hidden;
    color: var(--white);
  }
  .edge-band {
    position: absolute;
    left: 0;
    top: 0;
    width: 12px;
    height: 100%;
    background: linear-gradient(to bottom, var(--cyan) 0%, var(--cyan) 72%, var(--white) 72%, var(--white) 100%);
  }
  .back-brand {
    position: absolute;
    left: 44px;
    top: 34px;
    display: flex;
    align-items: center;
    gap: 14px;
  }
  .back-brand .brand-dot { width: 40px; height: 40px; }
  .back-brand .brand-name { font-size: 22px; }
  .contact-list {
    position: absolute;
    left: 44px;
    top: 130px;
    list-style: none;
    font-size: 13px;
    line-height: 1.55;
    color: var(--soft-white);
  }
  .contact-label { color: var(--cyan); margin-right: 4px; }
  .contact-email { font-weight: 600; color: var(--white); }
  .sales-title { margin-top: 8px; }
  .sales-email { color: var(--cyan); font-weight: 600; }
  .holder {
    position: absolute;
    right: 40px;
    bottom: 40px;
    text-align: left;
  }
  .holder-name {
    font-size: 30px;
    font-weight: 600;
    color: var(--cyan);
  }
  .holder-role {
    font-size: 14px;
    font-weight: 500;
    color: var(--white);
  }
</style>
</head>
<body>
<main class="canvas">

  <section class="card-front" aria-label="Business card front">
    <div class="circuit-texture" role="img" aria-label="Faint circuit board pattern background"></div>
    <div class="front-brand">
      <span class="brand-dot"></span>
      <p class="brand-name">Northglint<br>Technology</p>
      <p class="front-web">www.northglint-demo.com.sg</p>
    </div>
    <p class="tagline">
      <span class="tagline-lead">WE STRIVE TO</span>
      <span class="tagline-strong">SERVE YOU WELL</span>
    </p>
  </section>

  <section class="card-back" aria-label="Business card back">
    <div class="edge-band"></div>
    <div class="back-brand">
      <span class="brand-dot"></span>
      <p class="brand-name">Northglint<br>Technology</p>
    </div>
    <ul class="contact-list">
      <li><span class="contact-label">P:</span>+65 6000 1472</li>
      <li><span class="contact-label">F:</span>+65 9000 3825</li>
      <li><span class="contact-label">E:</span><span class="contact-email">tanwl@northglint-demo.com.sg</span></li>
      <li class="sales-title">Corporate Sales Enquiries :</li>
      <li class="sales-email">corporatesales@northglint-demo.com.sg</li>
    </ul>
    <div class="holder">
      <p class="holder-name">Tan Wei Lun</p>
      <p class="holder-role">Operations Manager</p>
    </div>
  </section>

</main>
</body>
</html>
```